Hop Bright Meadow Business Website Branding

Looking for a wordpress template design with CSS and HTML encoding. Current website can be seen at hopbrightmeadow.example.

WE ARE CURRENTLY IN PROCESS GETTING A LOGO DESIGN... I HAVE INCLUDED THE TOP POTENTIAL DESIGNS FOR REFERENCE TO HELP UNDERSTAND WHAT STYLE WE ARE LOOKING FOR...
NOTE: THE “PEBBLE CREW” LOGO WAS A PREVIOUS COMPANY WE OWNED SO YOU CAN GE A FEEL FOR THE TYPE OF DESIGNS WE HAVE USED IN THE PAST.

My blog will focus on making a connection with wild Florida, it’s wildlife, plants and animals... with an eye toward Florida conservation, nature adventure trips, and education... Content, photos and other merchandise will also be offered for sale.
I’m looking for a site design that incorporates Florida nature and wildlife/plants, with a fun “Old Florida” retro-adventure feel.
When they see this site it should speak to the import of natural Florida and the critical nature of the ecosystem here... while being instantly recognizable and iconic... IE: when I think of florida I think of water, plants, warmth, sunsets etc...

https://join.chatroomhub.example/t/lumexstudio-kzt4821/shared_invite/zt-pqwrt83m-hRnLvXaKoPzsYcB1Uq7JdM

Target Market(s)

Nature, Education, Conservation, Photography

Industry/Entity Type

Photographer

Coding

Coded - Design and coding required

Requirements
Must have
• Need to have site wide template design which generally includes a landing page and a general page template for other pages... Must include html and css encoding...
Should not have
• Any animals included in the site should be Florida native... IE: no African animals etc... This will require some research to ensure that if animals are included that they are part of the Florida ecosystem.

```html
<!DOCTYPE html>
<html lang="en">
<head>
<meta charset="utf-8">
<title>Hop Bright Meadow</title>
<link rel="stylesheet" href="https://fonts.googleapis.com/css2?family=Caveat+Brush&family=Lato:wght@300&family=Montserrat:wght@400;500&family=Roboto:wght@400&display=swap">
<style>
:root{
  --paper:#f1e5c3;
  --paper-dark:#e6d6ab;
  --red:#d8261d;
  --red-dark:#a8140f;
  --ink:#2a2420;
  --body:#4a4540;
  --muted:#6b655c;
  --rule:#d4c497;
  --frame-back:#3b2f24;
  --white:#ffffff;
  --footer:#0b0b0b;
  --footer-text:#d9d9d9;
  --footer-chip:#2a2a2a;
}
*{box-sizing:border-box;margin:0;padding:0}
html,body{width:1200px;height:3139px;overflow:hidden}
body{position:relative;background:radial-gradient(ellipse at 50% 30%,#f5ebcd 0%,var(--paper) 55%,var(--paper-dark) 100%);font-family:Roboto,Arial,sans-serif;color:var(--body)}
.abs{position:absolute}
.hand{font-family:"Caveat Brush",cursive}
.accent{color:var(--red)}

/* header */
.ribbon{left:0;top:90px;width:1200px;height:100px}
.logo-seat{left:486px;top:-20px;width:228px;height:240px;border-radius:0 0 114px 114px;background:#f1e3c1;box-shadow:0 4px 8px rgba(0,0,0,.15)}
.logo-ring{left:543px;top:20px;width:114px;height:114px;border:3px solid var(--red);border-radius:50%}
.brand{left:486px;top:128px;width:228px;text-align:center;font-size:30px;line-height:30px;color:var(--red)}
.nav a{position:absolute;top:130px;font-size:21px;color:var(--white);text-decoration:none;font-family:"Caveat Brush",cursive}

/* slider */
.slider-back{left:86px;top:202px;width:1030px;height:596px;background:var(--frame-back);box-shadow:0 8px 18px rgba(0,0,0,.35);border-radius:4px}
.slider-frame{left:100px;top:228px;width:1001px;height:542px;background:var(--white);box-shadow:0 4px 14px rgba(0,0,0,.4)}
.slider-photo{left:117px;top:248px;width:968px;height:499px;background:radial-gradient(ellipse at 60% 55%,#b49a52 0%,#6f6a35 30%,#3f5a22 60%,#2d3e1a 100%)}
.hero-title{left:151px;top:384px;font-size:60px;color:var(--white);text-shadow:0 2px 4px rgba(0,0,0,.4)}
.hero-sub{left:151px;top:460px;font-family:Lato,sans-serif;font-weight:300;font-size:23px;color:var(--white)}
.btn{display:block;background:var(--red);color:var(--white);border-radius:30px;text-align:center;font-family:"Caveat Brush",cursive;text-decoration:none}
.hero-btn{left:150px;top:514px;width:163px;height:56px;line-height:56px;font-size:21px}
.dots{left:140px;top:712px;display:flex;gap:4px}
.dots span{width:15px;height:15px;border:2px solid var(--white);border-radius:50%}
.dots span.on{background:#3d5a2a}

/* welcome */
.welcome-title{left:113px;top:893px;font-size:38px;color:var(--ink)}
.welcome-copy{left:112px;top:972px;width:488px;font-size:14px;line-height:26px;color:var(--body)}
.welcome-copy p+p{margin-top:26px}
.learn-btn{left:112px;top:1231px;width:195px;height:53px;line-height:53px;font-size:22px}
.feature-photo{left:668px;top:880px;width:400px;height:400px;border-radius:50%;border:14px solid var(--white);background:radial-gradient(circle at 55% 40%,#f06a36 0%,#d84a22 22%,#1f3b28 50%,#0f1e16 100%);box-shadow:0 2px 6px rgba(0,0,0,.15)}
.divider{left:112px;top:1336px;width:976px;height:1px;background:var(--rule)}

/* nature */
.section-title{left:0;width:1200px;text-align:center;font-size:44px;color:var(--ink)}
.underline{left:578px;width:44px;height:2px;background:var(--red)}
.card{width:260px;text-align:center}
.card .pic{width:200px;height:200px;margin:0 auto;border-radius:50%;border:5px solid var(--white)}
.card h3{margin-top:28px;font-family:"Caveat Brush",cursive;font-weight:400;font-size:24px;color:var(--ink)}
.card p{margin:14px auto 0;width:230px;font-size:14px;line-height:24px;color:var(--muted)}
.card .more{margin:14px auto 0;width:206px;border-top:1px solid var(--rule);border-bottom:1px solid var(--rule);height:54px;line-height:52px;font-family:"Caveat Brush",cursive;font-size:23px;color:var(--red)}
.card .more svg{vertical-align:-1px;margin-left:4px}

/* about band */
.band{left:70px;top:1950px;width:1064px;height:306px}
.avatar{left:157px;top:2011px;width:196px;height:196px;border-radius:50%;background:radial-gradient(circle at 40% 45%,#c99a6b 0%,#8a6a55 35%,#3d7f9e 70%,#2a5d7e 100%)}
.about-copy{left:394px;top:2028px;width:624px;font-size:13.8px;line-height:27.5px;color:var(--white);text-align:justify}

/* blog */
.post{width:313px}
.post .pic{height:200px;border:3px solid var(--white);border-radius:12px;box-shadow:0 1px 4px rgba(0,0,0,.2)}
.post .date{margin-top:16px;font-family:"Caveat Brush",cursive;font-size:21px;color:var(--red)}
.post p{margin-top:6px;font-size:14px;line-height:24px;color:var(--muted)}

/* footer */
.footer{left:0;top:2749px;width:1200px;height:390px;background:var(--footer);color:var(--footer-text)}
.foot-ring{left:189px;top:56px;width:126px;height:126px;border:3px solid var(--red);border-radius:50%}
.foot-brand{left:130px;top:185px;width:280px;text-align:center;font-size:34px;line-height:34px;color:var(--red)}
.foot-head{top:62px;font-family:"Caveat Brush",cursive;font-size:21px;color:var(--white)}
.links{left:445px;top:108px;list-style:none;font-family:Montserrat,sans-serif;font-size:12.5px;line-height:27.7px}
.links li::before{content:"\2192";margin-right:12px;color:var(--footer-text)}
.contact-row{left:642px;display:flex;align-items:center;gap:12px;font-family:Montserrat,sans-serif;font-size:14px;line-height:18px;color:var(--white)}
.chip{flex:none;width:36px;height:36px;border-radius:50%;background:var(--footer-chip);display:flex;align-items:center;justify-content:center}
.social{left:922px;display:flex;align-items:center;gap:24px;font-family:Montserrat,sans-serif}
.social .mark{width:12px;height:12px;border:2px solid var(--white);border-radius:50%}
.social small{display:block;font-size:12.5px;line-height:14px}
.social b{display:block;font-weight:400;font-size:17px;line-height:20px;color:var(--white)}
.foot-rule{left:112px;top:315px;width:976px;height:1px;background:#2c2c2c}
.copyright{left:0;top:345px;width:1200px;text-align:center;font-family:Montserrat,sans-serif;font-size:14px}
.code{left:1095px;top:342px;font-family:Montserrat,sans-serif;font-size:12px}
</style>
</head>
<body>

<header>
  <svg class="abs ribbon" viewBox="0 90 1200 100" width="1200" height="100" aria-hidden="true">
    <polygon points="71,104 136,104 136,150 80,150 90,127" fill="var(--red-dark)"/>
    <polygon points="1129,104 1064,104 1064,150 1120,150 1110,127" fill="var(--red-dark)"/>
    <rect x="112" y="117" width="976" height="55" fill="var(--red)"/>
    <rect x="112" y="117" width="976" height="2" fill="#e8534a"/>
  </svg>
  <div class="abs logo-seat"></div>
  <div class="abs logo-ring"></div>
  <div class="abs brand hand">Hop Bright<br>Meadow</div>
  <nav class="nav">
    <a style="left:151px">Home</a>
    <a style="left:244px">About Us</a>
    <a style="left:364px">Services</a>
    <a style="left:754px">Blog</a>
    <a style="left:831px">Testimonials</a>
    <a style="left:969px">Contact Us</a>
  </nav>
</header>

<section class="slider">
  <div class="abs slider-back"></div>
  <div class="abs slider-frame"></div>
  <div class="abs slider-photo" role="img" aria-label="Photo of a coiled python among green leaves"></div>
  <h1 class="abs hero-title hand" style="font-weight:400">Hop Bright Meadow</h1>
  <p class="abs hero-sub">Sed ut perspiciatis unde omnis iste natus</p>
  <a class="abs btn hero-btn">Read More</a>
  <div class="abs dots"><span></span><span></span><span class="on"></span><span></span><span></span></div>
</section>

<section class="welcome">
  <h2 class="abs welcome-title hand" style="font-weight:400">Welcome to <span class="accent">Hop Bright Meadow</span></h2>
  <div class="abs welcome-copy">
    <p>Sed ut perspiciatis unde omnis iste natus error sit voluptatem accusantium doloremque laudantium, totam rem aperiam, eaque ipsa quae ab illo inventore veritatis et quasi architecto beatae vitae dicta sunt explicabo. Nemo enim ipsam voluptatem quia voluptas sit aspernatur aut odit aut fugit, sed quia consequuntur magni dolores eos qui ratione voluptatem sequi nesciunt.</p>
    <p>Sed ut perspiciatis unde omnis iste natus error sit voluptatem accusantium doloremque laudantium, totam rem aperiam, eaque ipsa quae ab illo inventore veritatis et quasi architecto beatae vitae dicta sunt explicabo.</p>
  </div>
  <a class="abs btn learn-btn">Learn More</a>
  <div class="abs feature-photo" role="img" aria-label="Photo of a pink flamingo preening"></div>
  <div class="abs divider"></div>
</section>

<section class="nature">
  <h2 class="abs section-title hand" style="top:1383px;font-weight:400">Florida <span class="accent">Nature</span></h2>
  <div class="abs underline" style="top:1446px"></div>

  <div class="abs card" style="left:140px;top:1478px">
    <div class="pic" role="img" aria-label="Photo of purple blazing star wildflowers" style="background:radial-gradient(circle at 45% 40%,#b070c8 0%,#7a4e8e 30%,#4e6a2a 65%,#2f4a1c 100%)"></div>
    <h3>Florida Plants</h3>
    <p>Sed ut perspiciatis unde omnis iste natus error sit voluptatem accusanti doloremque laudantium</p>
    <div class="more">Read More<svg width="14" height="14" viewBox="0 0 14 14"><circle cx="7" cy="7" r="6" fill="none" stroke="currentColor" stroke-width="2"/><path d="M4 7h6M7.5 4.5 10 7 7.5 9.5" fill="none" stroke="currentColor" stroke-width="2"/></svg></div>
  </div>

  <div class="abs card" style="left:472px;top:1478px">
    <div class="pic" role="img" aria-label="Photo of a white peacock butterfly on dry leaves" style="background:radial-gradient(circle at 50% 45%,#e8e0cc 0%,#b29468 35%,#5a4a34 70%,#2e2720 100%)"></div>
    <h3>Florida Animals</h3>
    <p>Sed ut perspiciatis unde omnis iste natus error sit voluptatem accusanti doloremque laudantium</p>
    <div class="more">Read More<svg width="14" height="14" viewBox="0 0 14 14"><circle cx="7" cy="7" r="6" fill="none" stroke="currentColor" stroke-width="2"/><path d="M4 7h6M7.5 4.5 10 7 7.5 9.5" fill="none" stroke="currentColor" stroke-width="2"/></svg></div>
  </div>

  <div class="abs card" style="left:803px;top:1478px">
    <div class="pic" role="img" aria-label="Photo of red and yellow tropical flowers" style="background:radial-gradient(circle at 50% 50%,#e6d44a 0%,#e2465c 35%,#c92a44 65%,#3a5a24 100%)"></div>
    <h3>Florida Flowers</h3>
    <p>Sed ut perspiciatis unde omnis iste natus error sit voluptatem accusanti doloremque laudantium</p>
    <div class="more">Read More<svg width="14" height="14" viewBox="0 0 14 14"><circle cx="7" cy="7" r="6" fill="none" stroke="currentColor" stroke-width="2"/><path d="M4 7h6M7.5 4.5 10 7 7.5 9.5" fill="none" stroke="currentColor" stroke-width="2"/></svg></div>
  </div>
</section>

<section class="about">
  <svg class="abs band" viewBox="0 0 1064 306" width="1064" height="306" aria-hidden="true">
    <path fill="var(--red)" d="M8 14 L60 10 L110 16 L170 8 L230 14 L300 9 L360 15 L430 7 L500 13 L570 8 L640 15 L710 9 L780 14 L850 7 L920 13 L990 8 L1058 14 L1052 60 L1060 120 L1054 180 L1060 240 L1050 290 L990 294 L920 288 L850 296 L780 290 L710 297 L640 291 L570 298 L500 290 L430 296 L360 289 L290 297 L220 290 L150 296 L80 289 L12 296 L6 240 L0 180 L8 120 L2 60 Z"/>
  </svg>
  <div class="abs avatar" role="img" aria-label="Portrait photo of the naturalist at the beach"></div>
  <p class="abs about-copy">Hello nature lovers! I'm Marla Penwick, a wildlife educator, Florida Master Naturalist, nature writer and photographer, busy mama of three kiddos, a playful Havanese puppy, two very chubby guinea pigs, and a giant tree frog. I have a passion for all things nature and I adore living in Southwest Florida. I will always be a California girl, but from the moment I set foot in Florida, its wild beauty stole my heart. For the past 23 years, I have been fortunate to have some very unique and special experiences caring for many different species of animals and educating the public about wildlife and the environment.</p>
</section>

<section class="blog">
  <h2 class="abs section-title hand" style="top:2300px;font-weight:400">Latest <span class="accent">Blog</span></h2>
  <div class="abs underline" style="top:2362px"></div>

  <article class="abs post" style="left:112px;top:2397px">
    <div class="pic" role="img" aria-label="Photo of a white egret flying low over blue water" style="background:linear-gradient(180deg,#3f6fb8 0%,#2a4f95 50%,#1c3a78 100%)"></div>
    <div class="date">14.05.2020</div>
    <p>Sed ut perspiciatis unde omnis iste natus error sit voluptatem accusantium doloremque...</p>
  </article>
  <article class="abs post" style="left:443px;top:2397px">
    <div class="pic" role="img" aria-label="Photo of baby alligators resting on an adult alligator" style="background:linear-gradient(180deg,#5a5a4a 0%,#3b3d34 50%,#1f2220 100%)"></div>
    <div class="date">14.05.2020</div>
    <p>Sed ut perspiciatis unde omnis iste natus error sit voluptatem accusantium doloremque...</p>
  </article>
  <article class="abs post" style="left:775px;top:2397px">
    <div class="pic" role="img" aria-label="Photo of red and black butterflies on orange flowers" style="background:radial-gradient(circle at 50% 50%,#f6a23a 0%,#e9752a 40%,#6a8a2a 80%,#3c5a1e 100%)"></div>
    <div class="date">14.05.2020</div>
    <p>Sed ut perspiciatis unde omnis iste natus error sit voluptatem accusantium doloremque...</p>
  </article>
</section>

<footer class="abs footer">
  <div class="abs foot-ring"></div>
  <div class="abs foot-brand hand">Hop Bright<br>Meadow</div>

  <h4 class="abs foot-head" style="left:445px;font-weight:400">QUICK LINKS</h4>
  <ul class="abs links">
    <li>HOME</li><li>ABOUT US</li><li>SERVICES</li><li>BLOG</li><li>TESTIMONIALS</li><li>CONTACT US</li>
  </ul>

  <h4 class="abs foot-head" style="left:646px;font-weight:400">CONTACT US</h4>
  <div class="abs contact-row" style="top:106px">
    <span class="chip"><svg width="14" height="14" viewBox="0 0 24 24"><path fill="#fff" d="M6.6 10.8a15 15 0 0 0 6.6 6.6l2.2-2.2c.3-.3.7-.4 1-.2 1.1.4 2.3.6 3.6.6.6 0 1 .4 1 1V20c0 .6-.4 1-1 1A17 17 0 0 1 3 4c0-.6.4-1 1-1h3.5c.6 0 1 .4 1 1 0 1.3.2 2.5.6 3.6.1.3 0 .7-.2 1z"/></svg></span>
    +45 0101 2468
  </div>
  <div class="abs contact-row" style="top:155px">
    <span class="chip"><svg width="14" height="12" viewBox="0 0 14 12"><rect x="1" y="1" width="12" height="10" fill="none" stroke="#fff" stroke-width="1.5"/><path d="M1 1l6 5 6-5" fill="none" stroke="#fff" stroke-width="1.5"/></svg></span>
    info@hopbrightmeadow.example
  </div>
  <div class="abs contact-row" style="top:200px">
    <span class="chip"><svg width="12" height="16" viewBox="0 0 12 16"><path fill="#fff" d="M6 0a6 6 0 0 0-6 6c0 4.5 6 10 6 10s6-5.5 6-10a6 6 0 0 0-6-6zm0 8.2A2.2 2.2 0 1 1 6 3.8a2.2 2.2 0 0 1 0 4.4z"/></svg></span>
    <span>#154 Lorem Ipsum Dummy<br>Lorem Ipsum dummy</span>
  </div>

  <h4 class="abs foot-head" style="left:928px;font-weight:400">FOLLOW US</h4>
  <div class="abs social" style="top:108px"><span class="mark"></span><span><small>Like us on</small><b>Facefolio</b></span></div>
  <div class="abs social" style="top:165px"><span class="mark"></span><span><small>Follow us on</small><b>Chirper</b></span></div>
  <div class="abs social" style="top:222px"><span class="mark"></span><span><small>Follow us on</small><b>WorkLinks</b></span></div>

  <div class="abs foot-rule"></div>
  <p class="abs copyright">© Copyrights 2020-Hop Bright Meadow.All Rights Reserved.</p>
  <span class="abs code">C2</span>
</footer>

</body>
</html>
```